Suds Haven Laundromat Wordpress Design

We need a Wordpress website design for our laundromat, Suds Haven Atlanta, at www.sudshavenatlanta-example.com. We would like to have 6 pages: Home, About Us, Services, Locations, Reviews and Contact us. We will provide content for the text on each page. What we do: We are a full service laundromat that provides dry cleaning drop off, professional laundry services, wash dry fold and self service laundry to the local community. We would like to use the color scheme from our logo to convey a warm, safe, and bright business that caters to its diverse community.
Updates

I like the structure of this laundromat website: http://www.washtroveusa-example.com/ Using my logo and color scheme in the above referenced website is what. Am looking for. The photos attached to the project with the female model should be used as a primary focus and supplemented by actual photos of the equipment.

Target Market(s)

Our target market is a diverse group of people from Midtown Atlanta - LGBTQ community /Locals/Regulars that have been coming to laundromat for 30 years.

Industry/Entity Type

Laundromat

Coding

Coded - Design and coding required

Number of Pages Required

5+ page

Font styles to use
Sans Serif

Colors
0054AA
0677BA
7BADD7
CADEEF
E8F1F8

Requirements
Must have
• Feature this video on the main page: https://videohost-example.com/xq7Rm2bPz4k

```html
<!DOCTYPE html>
<html lang="en">
<head>
<meta charset="utf-8">
<title>Services | Suds Haven Atlanta</title>
<link href="https://fonts.googleapis.com/css2?family=Bebas+Neue&family=Montserrat:wght@400;500;600&display=swap" rel="stylesheet">
<style>
:root{
  --blue-deep:#0054AA;
  --blue:#0677BA;
  --blue-bright:#12A4DD;
  --blue-soft:#7BADD7;
  --blue-pale:#CADEEF;
  --blue-mist:#E8F1F8;
  --ink:#1f1f1f;
  --text:#3a3a3a;
  --footer:#2E4365;
  --rule:#e4e9ef;
  --white:#ffffff;
}
*{margin:0;padding:0;box-sizing:border-box}
html,body{width:1200px;height:2480px;overflow:hidden;background:var(--white)}
body{position:relative;font-family:"Montserrat",sans-serif;color:var(--text)}
.abs{position:absolute}

/* header */
.site-header{position:absolute;top:0;left:0;width:1200px;height:75px;background:var(--white);z-index:3}
.brand{position:absolute;left:103px;top:12px;display:flex;align-items:center;gap:10px}
.brand-dot{width:14px;height:14px;border-radius:50%;background:var(--blue-bright)}
.brand-name{font-family:"Bebas Neue",sans-serif;font-size:36px;line-height:1;color:var(--blue-deep);letter-spacing:.5px}
.brand-tag{position:absolute;left:167px;top:62px;font-size:10px;color:var(--blue-bright);letter-spacing:.2px}
.main-nav{position:absolute;top:0;left:525px;height:75px;display:flex}
.main-nav a{display:block;height:75px;line-height:84px;margin-right:38px;font-size:12.5px;color:var(--ink);text-decoration:none;position:relative}
.main-nav a.is-active{font-weight:600}
.main-nav a.is-active::after{content:"";position:absolute;left:0;right:0;bottom:0;height:4px;background:var(--blue)}
.nav-divider{position:absolute;left:1029px;top:19px;width:2px;height:38px;background:var(--blue)}
.social{position:absolute;top:32px;left:1049px;display:flex;gap:10px}
.social span{width:13px;height:13px;border-radius:50%;background:var(--ink)}

/* hero */
.hero{position:absolute;top:75px;left:0;width:1200px;height:610px;
  background:linear-gradient(90deg,#8a949c 0%,#c9ced0 18%,#c4e0d8 38%,#d9e6e0 50%,#c4e0d8 62%,#c9ced0 82%,#8a949c 100%)}
.hero-curve{position:absolute;top:580px;left:0;z-index:2}

/* breadcrumb */
.breadcrumb{position:absolute;top:698px;left:163px;font-size:12.5px;color:var(--ink)}
.breadcrumb .current{color:var(--blue);font-weight:600}

/* section title */
.section-title{position:absolute;top:790px;left:0;width:1200px;text-align:center;font-family:"Bebas Neue",sans-serif;font-size:36px;color:var(--ink);letter-spacing:.3px}
.section-title em{font-style:normal;color:var(--blue)}
.title-rule{position:absolute;top:834px;left:577px;width:46px;height:2px;background:var(--blue-bright)}

/* services */
.service-icon{position:absolute;width:165px;height:165px;border-radius:50%;background:var(--blue-mist)}
.service-title{position:absolute;font-family:"Bebas Neue",sans-serif;font-size:26px;color:var(--blue);letter-spacing:.2px}
.service-text{position:absolute;font-size:12.6px;line-height:24.6px;color:var(--text)}
.service-text p+p{margin-top:8px}
.divider{position:absolute;left:217px;width:780px;border-top:1px dashed var(--rule)}
.cta{position:absolute;left:524px;top:1835px;width:150px;height:41px;background:var(--blue-bright);color:var(--white);font-size:12.5px;font-weight:600;display:flex;align-items:center;justify-content:center;text-decoration:none}

/* footer */
.site-footer{position:absolute;top:1952px;left:0;width:1200px;height:528px;background:var(--footer);color:var(--white)}
.footer-brand{position:absolute;top:56px;left:0;width:1200px;text-align:center}
.footer-brand .name{font-family:"Bebas Neue",sans-serif;font-size:56px;line-height:1;color:var(--white);letter-spacing:1px}
.footer-brand .tag{font-size:12.5px;margin-top:4px;letter-spacing:.2px}
.f-rule{position:absolute;left:310px;width:580px;height:1px;background:rgba(255,255,255,.15)}
.footer-nav{position:absolute;top:226px;left:306px;display:flex;align-items:center}
.footer-nav a{color:var(--white);text-decoration:none;font-size:15px;margin-right:37px}
.footer-social{display:flex;gap:14px}
.footer-social span{width:30px;height:30px;border-radius:50%;background:var(--white)}
.contact-line{position:absolute;font-size:14px;line-height:24.5px;color:var(--white)}
.contact-line svg{position:absolute;left:-31px;top:3px}
.delivery{color:var(--blue-bright)}
.delivery b{font-weight:600}
.foot-rule{position:absolute;top:416px;left:163px;width:877px;height:1px;background:rgba(255,255,255,.15)}
.copyright{position:absolute;top:462px;left:0;width:1200px;text-align:center;font-size:12.5px}
.copyright b{font-weight:600}
</style>
</head>
<body>

<header class="site-header">
  <div class="brand"><span class="brand-dot"></span><span class="brand-name">Suds Haven</span></div>
  <div class="brand-tag">A FULL SERVICE LAUNDROMAT</div>
  <nav class="main-nav">
    <a href="#">HOME</a>
    <a href="#">ABOUT US</a>
    <a href="#" class="is-active">SERVICES</a>
    <a href="#">REVIEWS</a>
    <a href="#">CONTACT US</a>
  </nav>
  <div class="nav-divider"></div>
  <div class="social" aria-label="Social links"><span></span><span></span></div>
</header>

<div class="hero" role="img" aria-label="Photo of a woman in a blue dress walking through a laundromat lined with washers and dryers, retro sign on the wall"></div>
<svg class="hero-curve" width="1200" height="110" viewBox="0 0 1200 110" aria-hidden="true">
  <path d="M0 20 Q600 150 1200 30 L1200 110 L0 110 Z" fill="#ffffff"/>
  <path d="M0 20 Q600 150 1150 33 L1150 30 Q600 128 0 4 Z" fill="#0054AA"/>
</svg>

<div class="breadcrumb">HOME / <span class="current">SERVICES</span></div>

<h1 class="section-title">Our <em>Services</em></h1>
<div class="title-rule"></div>

<!-- wash dry fold -->
<div class="service-icon" style="left:236px;top:875px" role="img" aria-label="Icon of a folded shirt on a hanger"></div>
<h2 class="service-title" style="left:425px;top:888px">Wash Dry Fold</h2>
<div class="service-text" style="left:425px;top:929px;width:540px">
  <p>Tired, too much to do, own a business and need linens, sheets, towels, etc., cleaned? Don't worry, we can do your laundry for you! Have your laundry expertly washed, dried, and folded how you want it, we can even provide same day service. We also offer discounts for large orders.</p>
</div>
<div class="divider" style="top:1073px"></div>

<!-- professional -->
<h2 class="service-title" style="left:238px;top:1134px">Professional Laundry Services</h2>
<div class="service-text" style="left:238px;top:1175px;width:520px">
  <p>If you want to enjoy the perks of dry cleaning without all the chemicals, we offer a wash, dry, and press/iron service.&nbsp; You can relax knowing that your clothes will be flawlessly cleaned.</p>
</div>
<div class="service-icon" style="left:785px;top:1108px" role="img" aria-label="Icon of hangers above a washing machine and ironing board"></div>
<div class="divider" style="top:1306px"></div>

<!-- dry cleaning -->
<div class="service-icon" style="left:236px;top:1341px" role="img" aria-label="Icon of a dry cleaning attendant beside a jacket"></div>
<h2 class="service-title" style="left:425px;top:1367px">Dry Cleaning Drop Off</h2>
<div class="service-text" style="left:425px;top:1408px;width:555px">
  <p>Do you have clothing or linens that are made from delicate fabrics that aren't machine washable? We offer professional dry-cleaning services for our customers and businesses.</p>
</div>
<div class="divider" style="top:1539px"></div>

<!-- self service -->
<h2 class="service-title" style="left:238px;top:1582px">Self Service Laundry</h2>
<div class="service-text" style="left:238px;top:1623px;width:540px">
  <p>With over 40 well maintained self-service washers and dryers laundry will be a thing of the past! We now have CoinTap a free app. you download on your phone making quarters obsolete. Whether you need to wash a comforter or a load of baby clothes we have a working machine for you, so you can finish your laundry quickly!</p>
  <p>Meanwhile, you can relax in a clean and cared for environment. We offer free WiFi, arcade and vending machines, soap machines, plenty of parking, and there are some great restaurants in the mall we are located in.</p>
</div>
<div class="service-icon" style="left:785px;top:1574px" role="img" aria-label="Icon of a sparkling washing machine with stacked towels"></div>

<a class="cta" href="#">Contact Us Today</a>

<footer class="site-footer">
  <div class="footer-brand">
    <div class="name">SUDS HAVEN</div>
    <div class="tag">A FULL SERVICE LAUNDROMAT</div>
  </div>
  <div class="f-rule" style="top:198px"></div>
  <nav class="footer-nav">
    <a href="#">Home</a>
    <a href="#">About Us</a>
    <a href="#">Services</a>
    <a href="#">Reviews</a>
    <a href="#">Contact Us</a>
    <div class="footer-social" aria-label="Social links"><span></span><span></span></div>
  </nav>
  <div class="f-rule" style="top:280px"></div>

  <div class="contact-line" style="left:277px;top:318px;width:320px">
    <svg width="18" height="18" viewBox="0 0 18 18" fill="none" stroke="#fff" stroke-width="1.2"><circle cx="9" cy="9" r="7.5"/><path d="M1.5 9h15M9 1.5c3 3 3 12 0 15M9 1.5c-3 3-3 12 0 15"/></svg>
    Brightwater Plaza, 2210 Juniper Ridge Ave NE., # 118, Atlanta, GA 30399
  </div>
  <div class="contact-line" style="left:276px;top:376px">
    <svg width="18" height="18" viewBox="0 0 18 18" fill="none" stroke="#fff" stroke-width="1.2"><path d="M3 2l3 0 1.5 4-2 1.5c1 2.2 2.8 4 5 5L12 10.5l4 1.5v3c0 .8-.7 1.5-1.5 1.5C8 16.5 1.5 10 1.5 3.5 1.5 2.7 2.2 2 3 2z"/></svg>
    (404) 555-0187
  </div>
  <div class="contact-line" style="left:611px;top:318px;width:360px">
    <div class="delivery"><b>Delivery Available*</b> please contact us for details</div>
    <div style="margin-top:8px">Covid 19 hours – open 7 days a week 8 am to 8 pm<br>Last wash begins 6:30 pm</div>
  </div>
  <div class="foot-rule"></div>
  <div class="copyright">Copyright © 2021 <b>Suds Haven Atlanta</b>. All Rights Reserved.</div>
</footer>

</body>
</html>
```